Website improvements and Adding Functionalities at https://mervo.site/tarnovex

1.Search functionality
2.Payment process functionality
3. Application configuration
4. Registration functionality activation
5. Chat functionality
6.Language switching functionality (Portuguese & French)
7.Bespoke interactive modules
8. Automated web scraping and data synchronisation mechanisms
9. News Page
10.Webinar facilities
11. Basic SEO optimisation
12. Speed and performance optimisation
13. Security configuration
14. Google Analytics integration
15. Cross-browser and mobile testing
16. Website deployment and launch support

Target Market(s)

My target markets are companies, investors, suppliers and professionals with an interest in the Mozambican oil and gas sector

Industry/Entity Type

Oil and Gas

Coding

Coded - Design and coding required

Number of Pages Required

1 page

Requirements
Must have
• Improve the existing page at https://mervo.site/tarnovex and add the following features to it: 1. Search functionality 2. Payment process functionality 3. Application configuration 4. Activation of registration functionality 5. Chat functionality 6. Language switching functionality (Portuguese & French) 7. Bespoke interactive modules 8. Automated web scraping and data synchronisation mechanisms 9. News Page

```html
<!DOCTYPE html>
<html lang="en">
<head>
<meta charset="utf-8">
<title>Tarnovex – Mozambique Oil & Gas Intelligence</title>
<link href="https://fonts.googleapis.com/css2?family=Outfit:wght@400;500;600&family=Lato:wght@400;700&display=swap" rel="stylesheet">
<style>
:root{
  --orange:#ec4e26;
  --navy:#2f2a4a;
  --ink:#333;
  --muted:#555;
  --cream:#f4f0ea;
  --white:#fff;
  --purple:#4a3f68;
}
*{box-sizing:border-box;margin:0;padding:0}
html,body{width:1200px;height:3424px;overflow:hidden}
body{position:relative;font-family:"Lato",sans-serif;color:var(--ink);background:var(--white)}
section,header,footer{position:absolute;left:0;width:1200px}
h1,h2,h3,.brand,.btn,.item-box{font-family:"Outfit",sans-serif}
.btn{display:inline-flex;align-items:center;justify-content:center;background:var(--orange);color:var(--white);border-radius:30px;font-size:17px;font-weight:500;text-decoration:none}
.accent{color:var(--orange)}
.rule{display:block;width:106px;height:3px;background:var(--orange)}

/* header */
.site-header{top:0;height:120px;background:var(--white)}
.topbar{position:absolute;left:355px;top:0;width:845px;height:33px;background:var(--orange);clip-path:polygon(14px 0,100% 0,100% 100%,0 100%);display:flex;align-items:center;color:var(--white);font-size:14px;padding-left:50px;gap:34px}
.topbar .sep{width:1px;height:18px;background:rgba(255,255,255,.8)}
.topbar span{display:flex;align-items:center;gap:8px}
.social-dot{width:20px;height:20px;border-radius:50%;background:var(--white);display:inline-block}
.brand-block{position:absolute;left:110px;top:14px;width:180px;text-align:center}
.brand-mark{width:50px;height:50px;border-radius:50%;background:var(--navy);margin:0 auto 8px}
.brand{font-weight:600;font-size:15px;color:var(--navy);letter-spacing:1px}
.nav{position:absolute;left:297px;top:66px;display:flex;gap:21px;font-size:15px;color:#222}

/* hero */
.hero{top:120px;height:566px;background:radial-gradient(circle at 20% 70%,#3a6a8a 0%,transparent 35%),radial-gradient(circle at 85% 30%,#c98a3a 0%,transparent 30%),linear-gradient(135deg,#0d2438,#143b57 50%,#0a1c2c)}
.hero-panel{position:absolute;left:170px;top:102px;width:860px;height:316px;background:rgba(10,15,25,.72);border-radius:14px;text-align:center;color:var(--white)}
.hero h1{font-size:46px;font-weight:500;line-height:60px;margin-top:12px}
.hero p{font-size:16.5px;line-height:26px;width:720px;margin:24px auto 0}
.hero .btn{width:186px;height:47px;margin-top:25px}

/* about */
.about{top:686px;height:519px}
.about h2{position:absolute;left:112px;top:76px;font-size:43px;font-weight:500;color:var(--navy)}
.about .rule{position:absolute;left:112px;top:140px}
.about .copy{position:absolute;left:112px;top:176px;width:445px;font-size:14px;line-height:26px;text-align:justify;color:var(--muted)}
.about .copy p+p{margin-top:8px}
.about .btn{position:absolute;left:112px;top:385px;width:142px;height:47px}
.about .photo-back{position:absolute;left:652px;top:94px;width:446px;height:338px;border-radius:26px;background:var(--navy)}
.about .photo{position:absolute;left:643px;top:84px;width:446px;height:338px;border-radius:26px;background:linear-gradient(180deg,#f6a23c 0%,#e4742a 55%,#7a3418 100%)}

/* access */
.access{top:1205px;height:815px;background:var(--cream)}
.section-title{position:absolute;left:0;width:100%;text-align:center;font-size:44px;font-weight:500;color:var(--navy)}
.access .section-title{top:74px}
.access .rule,.unique .rule{position:absolute;left:547px}
.access .rule{top:141px}
.hub-ring{position:absolute;left:451px;top:217px;width:300px;height:300px;border-radius:50%;background:var(--navy)}
.hub-photo{position:absolute;left:461px;top:227px;width:280px;height:280px;border-radius:50%;background:linear-gradient(180deg,#c8a6c4 0%,#8ea1c6 50%,#3c4a66 100%)}
.item-box{position:absolute;width:214px;height:84px;background:var(--white);border-radius:10px;box-shadow:0 3px 8px rgba(0,0,0,.12);display:flex;align-items:center;justify-content:center;text-align:center;font-size:17px;line-height:25px;color:#222;padding:0 14px}
.item-icon{position:absolute;width:86px;height:86px;margin:-43px 0 0 -43px;border-radius:50%;background:var(--white);border:3px solid var(--navy);display:flex;align-items:center;justify-content:center}
.arrow{position:absolute;width:0;height:0;border-left:8px solid transparent;border-right:8px solid transparent;border-top:13px solid var(--orange)}

/* unique */
.unique{top:2020px;height:592px}
.unique .section-title{top:76px}
.unique .rule{top:142px}
.feature{position:absolute;width:300px;text-align:center}
.feature-circle{width:146px;height:146px;border-radius:50%;background:var(--white);box-shadow:0 6px 18px rgba(0,0,0,.12);margin:0 auto;display:flex;align-items:center;justify-content:center}
.feature h3{font-size:23px;font-weight:500;line-height:30px;color:#222;margin-top:30px}
.feature p{font-size:14.5px;line-height:23px;color:var(--muted);margin-top:16px}

/* how */
.how{top:2612px;height:404px;background:linear-gradient(180deg,#4c416c,#3e3560 60%,#4a3e63);text-align:center;color:var(--white)}
.how h2{font-size:44px;font-weight:500;margin-top:76px}
.how .rule{margin:10px auto 0}
.how p{font-size:16.5px;line-height:26px;width:870px;margin:22px auto 0}
.how .btn{width:186px;height:47px;margin-top:24px}
.chat-fab{position:absolute;left:1000px;top:356px;width:90px;height:90px;border-radius:50%;background:var(--white);box-shadow:0 4px 14px rgba(0,0,0,.2);display:flex;align-items:center;justify-content:center;z-index:2}

/* footer */
.site-footer{top:3016px;height:408px}
.footer-brand{position:absolute;left:110px;top:86px;width:230px;text-align:center}
.footer-brand .brand-mark{width:60px;height:60px}
.newsletter{position:absolute;left:110px;top:251px;width:262px;height:44px;border:1px solid #ccc;border-radius:6px;display:flex;align-items:center;justify-content:space-between;padding-left:14px;font-size:14px;color:#444}
.newsletter .send{width:46px;height:44px;margin-right:-1px;border-radius:6px;background:var(--orange);display:flex;align-items:center;justify-content:center}
.footer-col{position:absolute;top:86px}
.footer-col h3{font-size:18px;font-weight:400;color:var(--navy);margin-bottom:14px}
.footer-col ul{list-style:none}
.footer-col li{font-size:14px;color:#333;height:34.5px;display:flex;align-items:flex-start;gap:14px}
.footer-col li::before{content:"";width:8px;height:8px;border-radius:50%;background:var(--orange);margin-top:4px}
.contact li::before{display:none}
.contact li{gap:10px;height:45px}
.contact .ic{width:16px;height:16px;border-radius:50%;background:var(--orange);flex:none}
.footer-line{position:absolute;left:110px;top:364px;width:980px;height:1px;background:#ccc}
.footer-social{position:absolute;left:110px;top:375px;display:flex;gap:14px}
.footer-social i{width:22px;height:22px;border-radius:50%;background:var(--navy)}
.copyright{position:absolute;right:110px;top:380px;font-size:14px;color:#333}
</style>
</head>
<body>

<header class="site-header">
  <div class="topbar">
    <span><svg width="16" height="16" viewBox="0 0 24 24" fill="#fff"><path d="M6.6 10.8a15 15 0 0 0 6.6 6.6l2.2-2.2a1 1 0 0 1 1-.25 11 11 0 0 0 3.6.6 1 1 0 0 1 1 1V20a1 1 0 0 1-1 1A17 17 0 0 1 3 4a1 1 0 0 1 1-1h3.5a1 1 0 0 1 1 1c0 1.25.2 2.45.6 3.6a1 1 0 0 1-.25 1z"/></svg>+1 555 010 0199</span>
    <i class="sep"></i>
    <span><svg width="18" height="14" viewBox="0 0 18 14" fill="none" stroke="#fff" stroke-width="1.6"><rect x="1" y="1" width="16" height="12"/><path d="M1 1l8 6 8-6"/></svg>info@tarnovex.site</span>
    <i class="sep"></i>
    <span><svg width="20" height="20" viewBox="0 0 24 24" fill="none" stroke="#fff" stroke-width="2"><circle cx="10" cy="10" r="7"/><path d="M15 15l6 6"/></svg></span>
    <i class="sep"></i>
    <span><i style="width:30px;height:18px;background:#2b3a8c;display:inline-block"></i>EN ▾</span>
    <i class="sep"></i>
    <span><i class="social-dot"></i><i class="social-dot"></i><i class="social-dot"></i></span>
  </div>
  <div class="brand-block">
    <div class="brand-mark"></div>
    <div class="brand">TARNOVEX CO</div>
  </div>
  <nav class="nav">
    <span>Home</span><span>Industry Insights</span><span>Oil &amp; Gas Opportunities</span><span>Supplier &amp; Company Network</span><span>Register</span><span>Legal Framework</span>
  </nav>
</header>

<section class="hero" role="img" aria-label="Glowing circuit board background with orange light points">
  <div class="hero-panel">
    <h1>Access Mozambique’s Oil &amp; Gas Industry<br>Intelligence in One Platform</h1>
    <p>Tarnovex is a modern online connection and consulting platform designed to facilitate access to the Mozambican Oil and Gas industry through premium industry insights, supplier information, tenders, legal frameworks, and strategic project data.</p>
    <a class="btn">Register Now</a>
  </div>
</section>

<section class="about">
  <h2>What is <span class="accent">Tarnovex?</span></h2>
  <span class="rule"></span>
  <div class="copy">
    <p>Tarnovex is a unique online platform built to connect businesses, investors, suppliers, and professionals with valuable information about the Mozambican Oil &amp; Gas sector.</p>
    <p>Through a secure digital paywall system, users gain access to organized, up-to-date, and carefully selected industry information that supports better decision-making, market understanding, and business opportunities within Mozambique’s growing hydrocarbons industry.</p>
  </div>
  <a class="btn">Read More</a>
  <div class="photo-back"></div>
  <div class="photo" role="img" aria-label="Offshore oil platform and pipelines at sunset over the sea"></div>
</section>

<section class="access">
  <h2 class="section-title">What You <span class="accent">Will Access</span></h2>
  <span class="rule"></span>
  <div class="hub-ring"></div>
  <div class="hub-photo" role="img" aria-label="Gas processing plant towers under a pink evening sky"></div>

  <div class="item-box" style="left:151px;top:184px">Hydrocarbon Industry Information</div>
  <div class="item-box" style="left:112px;top:303px">Main Gas Projects</div>
  <div class="item-box" style="left:145px;top:440px">Supplier &amp; Company Database</div>
  <div class="item-box" style="left:231px;top:569px">Industry Contacts</div>
  <div class="item-box" style="left:496px;top:642px">Tender Opportunities</div>
  <div class="item-box" style="left:755px;top:571px">Ownership &amp; Access</div>
  <div class="item-box" style="left:843px;top:451px">Legal Framework</div>
  <div class="item-box" style="left:873px;top:309px">Local Company Capacity</div>
  <div class="item-box" style="left:847px;top:188px">Tender Application Guidance</div>

  <div class="item-icon" style="left:408px;top:242px"><svg width="38" height="38" viewBox="0 0 38 38" fill="none" stroke="#ec4e26" stroke-width="1.6"><path d="M4 34h30M8 34V18h6v16M17 34V12h6v22M26 34V20h6v14"/></svg></div>
  <div class="item-icon" style="left:367px;top:362px"><svg width="38" height="38" viewBox="0 0 38 38" fill="none" stroke="#ec4e26" stroke-width="1.6"><rect x="6" y="8" width="26" height="22" rx="2"/><path d="M6 14h26M11 20h10M11 25h16"/></svg></div>
  <div class="item-icon" style="left:400px;top:483px"><svg width="38" height="38" viewBox="0 0 38 38" fill="none" stroke="#ec4e26" stroke-width="1.6"><path d="M4 20l8-8 7 5 7-5 8 8-10 10-5-4-5 4z"/></svg></div>
  <div class="item-icon" style="left:486px;top:568px"><svg width="38" height="38" viewBox="0 0 38 38" fill="none" stroke="#ec4e26" stroke-width="1.6"><circle cx="20" cy="13" r="6"/><path d="M4 30h8l6 3 14-6"/></svg></div>
  <div class="item-icon" style="left:605px;top:600px"><svg width="38" height="38" viewBox="0 0 38 38" fill="none" stroke="#ec4e26" stroke-width="1.6"><path d="M19 6l2 5 5 1-4 3 1 5-4-3-4 3 1-5-4-3 5-1z"/><path d="M4 30h8l6 3 14-6"/></svg></div>
  <div class="item-icon" style="left:723px;top:569px"><svg width="38" height="38" viewBox="0 0 38 38" fill="none" stroke="#ec4e26" stroke-width="1.6"><circle cx="12" cy="12" r="5"/><circle cx="26" cy="12" r="5"/><path d="M6 32v-6l6-6 7 6 7-6 6 6v6"/></svg></div>
  <div class="item-icon" style="left:803px;top:483px"><svg width="38" height="38" viewBox="0 0 38 38" fill="none" stroke="#ec4e26" stroke-width="1.6"><rect x="9" y="5" width="20" height="26" rx="2"/><path d="M13 12h12M13 17h12M13 22h8"/></svg></div>
  <div class="item-icon" style="left:832px;top:367px"><svg width="38" height="38" viewBox="0 0 38 38" fill="none" stroke="#ec4e26" stroke-width="1.6"><circle cx="19" cy="19" r="7"/><circle cx="19" cy="19" r="13" stroke-dasharray="3 4"/></svg></div>
  <div class="item-icon" style="left:803px;top:246px"><svg width="38" height="38" viewBox="0 0 38 38" fill="none" stroke="#ec4e26" stroke-width="1.6"><path d="M19 4v30M12 10h14l3 3-3 3H12zM26 20H12l-3 3 3 3h14"/></svg></div>

  <i class="arrow" style="left:457px;top:271px;transform:rotate(-20deg)"></i>
  <i class="arrow" style="left:425px;top:360px;transform:rotate(90deg)"></i>
  <i class="arrow" style="left:451px;top:442px;transform:rotate(200deg)"></i>
  <i class="arrow" style="left:515px;top:500px;transform:rotate(-60deg)"></i>
  <i class="arrow" style="left:594px;top:524px"></i>
  <i class="arrow" style="left:677px;top:497px;transform:rotate(60deg)"></i>
  <i class="arrow" style="left:735px;top:438px;transform:rotate(160deg)"></i>
  <i class="arrow" style="left:758px;top:360px;transform:rotate(-90deg)"></i>
  <i class="arrow" style="left:732px;top:273px;transform:rotate(20deg)"></i>
</section>

<section class="unique">
  <h2 class="section-title">Why Tarnovex Is <span class="accent">Unique</span></h2>
  <span class="rule"></span>
  <svg style="position:absolute;left:0;top:0" width="1200" height="400" fill="none" stroke="#2f2a4a" stroke-width="2" stroke-dasharray="9 7">
    <path d="M318 292 C 400 335, 480 335, 540 315"/>
    <path d="M672 228 C 750 200, 820 200, 885 230"/>
  </svg>
  <div class="feature" style="left:96px;top:189px">
    <div class="feature-circle"><svg width="72" height="72" viewBox="0 0 72 72" fill="none" stroke="#ec4e26" stroke-width="2"><circle cx="36" cy="36" r="10"/><circle cx="36" cy="36" r="18" stroke="#2f2a4a"/><path d="M36 10v8M36 54v8M10 36h8M54 36h8" stroke="#2f2a4a"/></svg></div>
    <h3>Up-to-Date Industry<br>Intelligence</h3>
    <p>Receive frequent updates about<br>developments in Mozambique’s Oil<br>&amp; Gas sector.</p>
  </div>
  <div class="feature" style="left:451px;top:189px">
    <div class="feature-circle"><svg width="72" height="72" viewBox="0 0 72 72" fill="none" stroke="#ec4e26" stroke-width="2"><circle cx="36" cy="24" r="10"/><path d="M31 24l4 4 7-7"/><path d="M10 40l8 20h8M62 40l-8 20h-8" stroke="#2f2a4a"/></svg></div>
    <h3>High-Quality Curated<br>Information</h3>
    <p>Access carefully selected and<br>synthesized information tailored to<br>industry stakeholders.</p>
  </div>
  <div class="feature" style="left:806px;top:189px">
    <div class="feature-circle"><svg width="72" height="72" viewBox="0 0 72 72" fill="none" stroke="#ec4e26" stroke-width="2"><rect x="26" y="10" width="24" height="30" rx="2"/><path d="M31 18h14M31 24h14M31 30h9"/><path d="M10 52l12-6 14 6 18-8" stroke="#2f2a4a"/></svg></div>
    <h3>Time-Saving Access</h3>
    <p>Avoid spending hours searching<br>through scattered online sources with<br>organized and accessible content in<br>one platform.</p>
  </div>
</section>

<section class="how" role="img" aria-label="Offshore platforms at sea under a purple tint">
  <h2>How The Platform Works</h2>
  <span class="rule"></span>
  <p>The platform operates through a secure automated payment system that grants registered users access to premium and exclusive content. By subscribing, users receive organized industry intelligence designed to save time, improve market access, and support strategic business growth within Mozambique’s energy sector.</p>
  <a class="btn">Register Now</a>
  <div class="chat-fab"><svg width="48" height="44" viewBox="0 0 48 44"><path d="M6 4h36a4 4 0 0 1 4 4v22a4 4 0 0 1-4 4H20l-10 8v-8H6a4 4 0 0 1-4-4V8a4 4 0 0 1 4-4z" fill="#2f2a4a"/><path d="M13 15h22M13 23h16" stroke="#fff" stroke-width="3" stroke-linecap="round"/></svg></div>
</section>

<footer class="site-footer">
  <div class="footer-brand">
    <div class="brand-mark"></div>
    <div class="brand">TARNOVEX CO</div>
  </div>
  <div class="newsletter">Enter email address<span class="send"><svg width="22" height="22" viewBox="0 0 24 24" fill="#fff"><path d="M22 2L2 10l8 3 3 9z"/></svg></span></div>

  <div class="footer-col" style="left:456px">
    <h3>Quick Links</h3>
    <ul><li>Home</li><li>About Us</li><li>Platform Features</li><li>Supplier Directory</li><li>Industry Projects</li><li>Tender Opportunities</li><li>Industry News</li></ul>
  </div>
  <div class="footer-col" style="left:675px">
    <h3>Support</h3>
    <ul><li>Help Center</li><li>Live Chat</li><li>Account Login</li><li>Payment &amp; Billing</li><li>Privacy Policy</li><li>Terms &amp; Conditions</li><li>Cookie Policy</li></ul>
  </div>
  <div class="footer-col contact" style="left:912px">
    <h3>Contact Us</h3>
    <ul>
      <li><i class="ic"></i>Maputo, Mozambique</li>
      <li><i class="ic"></i>info@tarnovex.site</li>
      <li><i class="ic"></i>+1 555 010 0199</li>
      <li><i class="ic"></i>9–17 Opening hours</li>
    </ul>
  </div>

  <div class="footer-line"></div>
  <div class="footer-social"><i></i><i></i><i></i></div>
  <div class="copyright">© 2026 Tarnovex Co. All Rights Reserved.</div>
</footer>

</body>
</html>
```